Pebblecroft dog Kennel -Loyalty Card

We are a bod boarding and training Kennel located in Egypt and we would like to design a member loyalty card. The card need to be fun, funky. I would like the logo to appear on the card. On the back side we will list the benefits and on the bottom side of the card will will have the logos of our partner companies

Target Market(s)

clientele from dog lovers. Age 25 and above. 65% women.

Industry/Entity Type

Training

Font styles to use
Sans Serif

Colors
0555a3
33a6d7
0792cd

Requirements
Must have
• Pebblecroft Logo and bleu colours.
Nice to have
• a dog figure
Should not have
• dark serious colours or aggressive looking dogs or dog breeds

```html
<!DOCTYPE html>
<html lang="en">
<head>
<meta charset="utf-8">
<title>Pebblecroft dog Kennel – Loyalty Card</title>
<link rel="stylesheet" href="https://fonts.googleapis.com/css2?family=Open+Sans:wght@400;600;700&display=swap">
<style>
  :root {
    --stage: #1c1c1c;
    --white: #ffffff;
    --ink: #1a1a1a;
    --navy: #2457a0;
    --deep-blue: #0555a3;
    --mid-blue: #0792cd;
    --sky-blue: #33a6d7;
    --orange: #e87722;
    --partner-blue: #2d7fa8;
    --partner-purple: #6a4fa3;
  }
  * { box-sizing: border-box; margin: 0; padding: 0; }
  html, body {
    width: 1200px; height: 900px; overflow: hidden;
    background: var(--stage);
    font-family: "Open Sans", Arial, sans-serif;
  }
  .canvas { position: relative; width: 1200px; height: 900px; }

  .card {
    position: absolute; top: 265px;
    width: 451px; height: 262px;
    border-radius: 12px; overflow: hidden;
  }
  .card-front { left: 132px; background: var(--white); }
  .card-back {
    left: 633px;
    background: linear-gradient(180deg, var(--sky-blue) 0%, var(--mid-blue) 60%);
  }
  .wave { position: absolute; left: 0; top: 0; width: 100%; height: 100%; }

  /* brand name */
  .brand { position: absolute; display: flex; align-items: center; gap: 8px; }
  .brand-mark { background: var(--orange); }
  .brand-name { font-weight: 700; color: var(--navy); }
  .card-front .brand { left: 30px; top: 78px; flex-direction: column; gap: 10px; width: 160px; }
  .card-front .brand-mark { width: 40px; height: 40px; }
  .card-front .brand-name { font-size: 25px; }
  .card-back .brand { left: 48px; top: 200px; }
  .card-back .brand-mark { width: 14px; height: 14px; }
  .card-back .brand-name { font-size: 15px; color: var(--white); }

  /* contact block */
  .contact { position: absolute; left: 232px; top: 53px; color: var(--ink); }
  .contact-name { font-size: 19px; font-weight: 600; color: var(--navy); line-height: 1.2; }
  .contact-role { font-size: 13px; color: var(--orange); margin-top: 1px; }
  .contact-address { font-size: 13px; margin-top: 14px; }
  .contact-lines { list-style: none; margin-top: 10px; font-size: 13px; }
  .contact-lines li { display: flex; align-items: center; gap: 6px; line-height: 18px; }
  .contact-lines svg { flex: none; }

  /* benefits */
  .benefits {
    position: absolute; left: 42px; top: 43px;
    list-style: none; color: var(--white);
    font-size: 16px; font-weight: 600; line-height: 25px;
  }

  /* partner badges */
  .partners { position: absolute; right: 28px; top: 181px; display: flex; gap: 12px; }
  .partner-badge {
    width: 66px; height: 66px; border-radius: 4px;
    background: var(--white);
    display: flex; align-items: center; justify-content: center;
  }
  .partner-badge span { width: 36px; height: 36px; border-radius: 3px; margin-bottom: 10px; }
  .partner-badge.is-blue span { background: var(--partner-blue); }
  .partner-badge.is-purple span { background: var(--partner-purple); }
</style>
</head>
<body>
<main class="canvas">

  <section class="card card-front" aria-label="Loyalty card front">
    <svg class="wave" viewBox="0 0 451 262" preserveAspectRatio="none" aria-hidden="true">
      <path fill="var(--navy)" d="M0,237 C110,258 210,244 300,214 C370,192 420,188 451,188 L451,262 L0,262 Z"/>
      <path fill="var(--orange)" d="M0,217 C120,248 230,226 320,194 C380,176 420,175 451,177 L451,183 C405,182 365,188 305,208 C210,240 110,250 0,229 Z"/>
    </svg>

    <div class="brand">
      <span class="brand-mark"></span>
      <span class="brand-name">Pebblecroft</span>
    </div>

    <div class="contact">
      <p class="contact-name">Marlow Keane</p>
      <p class="contact-role">Managing Director</p>
      <p class="contact-address">PO Box 2217 Fernhill, OR 97140</p>
      <ul class="contact-lines">
        <li>
          <svg width="8" height="11" viewBox="0 0 8 11" aria-hidden="true"><rect x="0.75" y="0.75" width="6.5" height="9.5" rx="1.2" fill="none" stroke="var(--orange)" stroke-width="1.5"/><rect x="3" y="8" width="2" height="1" fill="var(--orange)"/></svg>
          <span>555-201-4388</span>
        </li>
        <li>
          <svg width="9" height="7" viewBox="0 0 9 7" aria-hidden="true"><rect width="9" height="7" fill="var(--orange)"/><path d="M0,0 L4.5,4 L9,0" fill="none" stroke="var(--white)" stroke-width="1"/></svg>
          <span>hello@pebblecroft.example</span>
        </li>
      </ul>
    </div>
  </section>

  <section class="card card-back" aria-label="Loyalty card back">
    <svg class="wave" viewBox="0 0 451 262" preserveAspectRatio="none" aria-hidden="true">
      <path fill="var(--deep-blue)" d="M0,175 C100,200 200,185 300,150 C370,130 420,125 451,125 L451,262 L0,262 Z"/>
      <path fill="var(--orange)" d="M0,160 C110,190 210,174 300,140 C370,117 420,117 451,119 L451,127 C410,126 370,131 300,151 C200,185 100,198 0,175 Z"/>
    </svg>

    <ul class="benefits">
      <li>5% discount on all 1 PawMart purchased</li>
      <li>10% discount on Suds &amp; Stroll services</li>
      <li>10% Discount on Pebblecroft training courses</li>
      <li>One free trial for Day Care service</li>
    </ul>

    <div class="brand">
      <span class="brand-mark"></span>
      <span class="brand-name">Pebblecroft</span>
    </div>

    <div class="partners" aria-label="Partner companies">
      <div class="partner-badge is-blue" role="img" aria-label="Partner badge"><span></span></div>
      <div class="partner-badge is-purple" role="img" aria-label="Partner badge"><span></span></div>
    </div>
  </section>

</main>
</body>
</html>
```